Wine Label for a Sweet Wine Called "Glimmo"

We need a wine label that will be used for both a sweet red and a sweet white wine. The very important thing to remember is the target market for these wines is: young American women who love sweet wines and they also spend a lot of their money on their hair, clothes, jewelry, nails. They LOVE Glimmo (Glimmo is a word used to describe flashy accessories, jewelry, decoration.) This label needs to be eye catching, showy, fun, glittery. Please put the brand name, "Glimmo," big, and then in smaller but still readable words underneath the label or somewhere on the label: Sweet, Sophisticated, Red (or white). (An example of what I mean is attached). To differentiate between the two color wines you can suggest color changes to differentiate between the red label and the white label but the label design itself should be the same. Ultimately, the label can be the exact same label for both white and red as long as it looks good on a white wine (a greenish/yellow wine in a clear glass bottle) and a red wine (a dark color wine in a dark bottle).

I've attached an example of the text size relationship between the word Glimmo and the words to go underneath or elsewhere on the label, but you can certainly play with this-- it is just a suggestion of the text size relationship, and definitely NOT at all mandatory that you use any of these fonts.

You can pick the size of the label but try to stay within normal wine label sizes, meaning don't go bigger than approx. 3.5 inches wide and 5 inches tall.

Target Market(s)

Young American women who love sweet wines and spend a lot of money on their hair, clothes, jewelry, nails. They love Glimmo (Glimmo is a word that means flashy accessories, jewelry, decoration)

Requirements
Must have
• It needs to be flashy, glittery, fun, eye catching, memorable
Nice to have
• It shouldn't be too too ultra feminine! The target market is strong independent women and we also have men who will buy it too.

```html
<!DOCTYPE html>
<html lang="en">
<head>
<meta charset="utf-8">
<title>Glimmo – Wine Labels</title>
<link rel="stylesheet" href="https://fonts.googleapis.com/css2?family=Abril+Fatface&family=Montserrat:wght@500&display=swap">
<style>
  :root {
    --page-bg: #ececec;
    --page-glow: #fafafa;
    --frame-line: #ffffff;
    --red-deep: #8c0f45;
    --red-mid: #c2356f;
    --red-light: #e48cad;
    --red-name: rgba(255, 236, 242, 0.92);
    --red-tag: rgba(255, 225, 236, 0.9);
    --white-deep: #a9bd6a;
    --white-mid: #cfdc9a;
    --white-light: #f3f6dc;
    --white-name: #7e9a4c;
    --white-tag: #8ea35e;
  }
  * { margin: 0; padding: 0; box-sizing: border-box; }
  html, body { width: 1200px; height: 1000px; overflow: hidden; }
  body {
    background: radial-gradient(ellipse at 50% 40%, var(--page-glow) 0%, var(--page-bg) 75%);
    position: relative;
  }
  .label {
    position: absolute;
    top: 250px;
    width: 340px;
    height: 480px;
  }
  .label--red { left: 220px; }
  .label--white { left: 640px; }
  .label__art { position: absolute; inset: 0; width: 100%; height: 100%; }
  .label__text {
    position: absolute;
    left: 0; right: 0;
    top: 285px;
    text-align: center;
  }
  .label__name {
    font-family: "Abril Fatface", "Playfair Display", serif;
    font-size: 80px;
    line-height: 1;
    font-weight: 400;
  }
  .label__tagline {
    margin-top: 12px;
    font-family: "Montserrat", sans-serif;
    font-weight: 500;
    font-size: 11px;
    letter-spacing: 3px;
    text-transform: uppercase;
  }
  .label--red .label__name { color: var(--red-name); }
  .label--red .label__tagline { color: var(--red-tag); }
  .label--white .label__name { color: var(--white-name); }
  .label--white .label__tagline { color: var(--white-tag); }
</style>
</head>
<body>

  <div class="label label--red">
    <svg class="label__art" viewBox="0 0 340 480" aria-hidden="false">
      <defs>
        <radialGradient id="red-glitter" cx="55%" cy="35%" r="75%">
          <stop offset="0" stop-color="var(--red-light)"/>
          <stop offset="0.45" stop-color="var(--red-mid)"/>
          <stop offset="1" stop-color="var(--red-deep)"/>
        </radialGradient>
      </defs>
      <path role="img" aria-label="Sparkling magenta glitter background with bokeh lights"
            fill="url(#red-glitter)"
            d="M18 0H322A18 18 0 0 0 340 18V462A18 18 0 0 0 322 480H18A18 18 0 0 0 0 462V18A18 18 0 0 0 18 0Z"/>
      <path fill="none" stroke="var(--frame-line)" stroke-width="2"
            d="M24 8H316A16 16 0 0 0 332 24V456A16 16 0 0 0 316 472H24A16 16 0 0 0 8 456V24A16 16 0 0 0 24 8Z"/>
    </svg>
    <div class="label__text">
      <h1 class="label__name">Glimmo</h1>
      <p class="label__tagline">Sweet | Red | Sophisticated</p>
    </div>
  </div>

  <div class="label label--white">
    <svg class="label__art" viewBox="0 0 340 480">
      <defs>
        <radialGradient id="white-glitter" cx="50%" cy="35%" r="75%">
          <stop offset="0" stop-color="var(--white-light)"/>
          <stop offset="0.5" stop-color="var(--white-mid)"/>
          <stop offset="1" stop-color="var(--white-deep)"/>
        </radialGradient>
      </defs>
      <path role="img" aria-label="Sparkling pale green-gold glitter background with bokeh lights"
            fill="url(#white-glitter)"
            d="M18 0H322A18 18 0 0 0 340 18V462A18 18 0 0 0 322 480H18A18 18 0 0 0 0 462V18A18 18 0 0 0 18 0Z"/>
      <path fill="none" stroke="var(--frame-line)" stroke-width="2"
            d="M24 8H316A16 16 0 0 0 332 24V456A16 16 0 0 0 316 472H24A16 16 0 0 0 8 456V24A16 16 0 0 0 24 8Z"/>
    </svg>
    <div class="label__text">
      <h2 class="label__name">Glimmo</h2>
      <p class="label__tagline">Sweet | White | Sophisticated</p>
    </div>
  </div>

</body>
</html>
```